Business Card for a Dental Office

The design should communicate integrity, quality and reliability. We also want the card look elegant, simple, but still stand out, different from the traditional-dental-office business card.

Industry/Entity Type

Business

```html
<!DOCTYPE html>
<html lang="en">
<head>
<meta charset="utf-8">
<title>Halden Dental Studio – Business Cards</title>
<link rel="stylesheet" href="https://fonts.googleapis.com/css2?family=Oswald:wght@500;600&family=Open+Sans:ital,wght@0,400;0,600;0,700;1,700&display=swap">
<style>
  :root {
    --backdrop: #3b3c40;
    --card: #ffffff;
    --card-back: #f3f3f3;
    --ink: #111111;
    --ink-soft: #222222;
    --gold: #8a6d1c;
    --gold-light: #b08d2a;
    --yellow: #e8d51e;
    --yellow-deep: #c9b40e;
    --dots: #333333;
  }
  * { box-sizing: border-box; margin: 0; padding: 0; }
  html, body { width: 1200px; height: 864px; overflow: hidden; }
  body { background: var(--backdrop); font-family: "Open Sans", sans-serif; color: var(--ink); }
  .canvas { position: relative; width: 1200px; height: 864px; overflow: hidden; }

  .card {
    position: absolute; width: 600px; height: 343px;
    box-shadow: 0 14px 30px rgba(0,0,0,.45);
    overflow: hidden;
  }

  /* Appointment card */
  .appointment-card { left: 200px; top: 60px; background: var(--card); }
  .brand-lockup { position: absolute; top: 30px; left: 0; right: 0; text-align: center; }
  .brand-row { display: inline-flex; align-items: center; gap: 10px; }
  .brand-mark { width: 26px; height: 26px; background: var(--ink); }
  .brand-name {
    font-family: "Oswald", sans-serif; font-weight: 600; font-size: 28px;
    letter-spacing: .5px; color: var(--ink); line-height: 1;
  }
  .brand-tagline {
    margin-top: 4px; font-weight: 700; font-size: 10.5px; letter-spacing: 1.6px;
    color: var(--gold); text-transform: uppercase;
  }
  .appointment-title {
    position: absolute; top: 108px; left: 0; right: 0; text-align: center;
    font-weight: 700; font-size: 22px; color: var(--yellow-deep);
    background: linear-gradient(180deg, #f2e23a, #c9b10a);
    -webkit-background-clip: text; background-clip: text; -webkit-text-fill-color: transparent;
  }
  .appointment-fields { position: absolute; top: 150px; left: 105px; right: 105px; }
  .field { display: flex; align-items: flex-end; height: 30px; font-weight: 700; font-size: 13px; color: var(--ink); }
  .field-label { white-space: nowrap; margin-right: 8px; }
  .field-line { flex: 1; border-bottom: 2px dotted var(--dots); margin-bottom: 4px; }
  .field-unit { margin: 0 8px; }
  .notice-band {
    position: absolute; left: 12px; right: 12px; bottom: 18px; height: 34px;
    background: linear-gradient(180deg, #f3e43c 0%, #d8c312 55%, #b9a50a 100%);
    display: flex; align-items: center; justify-content: center;
    font-style: italic; font-weight: 700; font-size: 16px; color: var(--ink);
  }

  /* Contact card */
  .contact-card { left: 300px; top: 470px; background: linear-gradient(135deg, #ffffff 0%, var(--card-back) 60%); }
  .contact-brand { position: absolute; top: 26px; left: 30px; }
  .contact-brand .brand-name { font-size: 30px; }
  .contact-brand .brand-tagline { font-size: 11.5px; letter-spacing: 1.8px; margin-top: 2px; }
  .person { position: absolute; top: 128px; left: 30px; }
  .person-name { font-weight: 600; font-size: 19px; color: var(--gold-light); line-height: 1.2; }
  .person-role { font-size: 14px; color: var(--ink-soft); }
  .address { position: absolute; top: 190px; left: 30px; font-size: 14px; line-height: 1.3; color: var(--ink-soft); }
  .contact-list { position: absolute; top: 250px; left: 30px; list-style: none; font-size: 14px; color: var(--ink-soft); }
  .contact-list li { display: flex; align-items: center; gap: 10px; height: 20px; }
  .contact-list svg { width: 12px; height: 12px; fill: var(--gold-light); flex: none; }
</style>
</head>
<body>
<main class="canvas">

  <section class="card appointment-card" aria-label="Appointment card">
    <header class="brand-lockup">
      <div class="brand-row">
        <span class="brand-mark" aria-hidden="true"></span>
        <span class="brand-name">HALDEN DENTAL STUDIO</span>
      </div>
      <p class="brand-tagline">Your smile is your gift to others</p>
    </header>
    <h2 class="appointment-title">Your Next Appointment is</h2>
    <div class="appointment-fields">
      <div class="field"><span class="field-label">Name :</span><span class="field-line"></span></div>
      <div class="field"><span class="field-label">Date :</span><span class="field-line"></span></div>
      <div class="field"><span class="field-label">Time :</span><span class="field-line"></span><span class="field-unit">AM</span><span class="field-line"></span><span class="field-unit">PM</span></div>
    </div>
    <p class="notice-band">If unable to keep appointment, kindly give 24hrs notice.</p>
  </section>

  <section class="card contact-card" aria-label="Contact card">
    <header class="contact-brand">
      <div class="brand-name">HALDEN DENTAL STUDIO</div>
      <p class="brand-tagline">Your smile is your gift to others</p>
    </header>
    <div class="person">
      <p class="person-name">Marcus Ellery</p>
      <p class="person-role">Managing Director</p>
    </div>
    <address class="address" style="font-style:normal">48 Larchmont Avenue<br>Northfield, NF 20418.</address>
    <ul class="contact-list">
      <li>
        <svg viewBox="0 0 24 24" aria-hidden="true"><path d="M6.6 10.8a15.1 15.1 0 0 0 6.6 6.6l2.2-2.2c.3-.3.7-.4 1-.2 1.1.4 2.3.6 3.6.6.6 0 1 .4 1 1V20c0 .6-.4 1-1 1A17 17 0 0 1 3 4c0-.6.4-1 1-1h3.5c.6 0 1 .4 1 1 0 1.3.2 2.5.6 3.6.1.3 0 .7-.2 1z"/></svg>
        <span>044-555 201 846</span>
      </li>
      <li>
        <svg viewBox="0 0 24 24" aria-hidden="true"><path d="M2 5h20v14H2z M2 5l10 8 10-8" stroke="#fff" stroke-width="1.5"/></svg>
        <span>hello@haldendental.com</span>
      </li>
      <li>
        <svg viewBox="0 0 24 24" aria-hidden="true"><path d="M10.6 13.4a1 1 0 0 1 0-1.4l4-4a1 1 0 1 1 1.4 1.4l-4 4a1 1 0 0 1-1.4 0zM8.5 19.5a4 4 0 0 1-5.7-5.7l3-3 1.4 1.4-3 3a2 2 0 0 0 2.9 2.9l3-3 1.4 1.4zm9.7-6.3-1.4-1.4 3-3a2 2 0 0 0-2.9-2.9l-3 3-1.4-1.4 3-3a4 4 0 0 1 5.7 5.7z"/></svg>
        <span>www.haldendental.com</span>
      </li>
    </ul>
  </section>

</main>
</body>
</html>
```